Luxury Wine Label for New Startup Winery

We need a wine label for our new winery startup. We have worked with a local designer but do not feel the resulting label / logo have the elevation required to present our brand as a luxury wine. Our winery is called "Quailbrook Vineyards" and we are focused on extremely high quality hand crafted artisan and estate wines from the Pacific Northwest.
We would like to see designs that utilize a tree line, or other imagery that represents the "Quailbrook" part of our company name. Another interesting feature could be wood grain.
A logo will be required based on your design so please design with this in mind:
This logo should be consistent with the wine bottle label design, and should be representative of our high end exclusive wine while giving a sense of place (Oregon/ Pacific Northwest.)
I will supply an image of the design we received from our local designer, PLEASE NOTE: in general we do like wood grain and tree line concepts but feel the execution was poorly done.
ATTN: Logo design should be suitable for use on: Bottles (Red wine/rose/white wine), Bussiness cards, vehicle signage, business signage, etc
P.S.:
If you have a design that is not outside the box we are still interested in seeing it.
Label is for a burgundy style bottle with a label height of 3.5 - 4" and a width of 3.5-4"
any label <= 4"x4" and >=3.5"x3.5" will be acceptable:
HOWEVER Width should be greater than or equal to height due to the bottle format
Target Market(s)
Wine enthusiasts with adequate discretionary budgets to afford $100 bottles of wine.
Industry/Entity Type
Wine / Winery
Requirements
Must have
- A sense of luxury, a feel of exclusivity, and a theme consistent with our product and brand name
Nice to have
- Tree line, wood grain or other wood themes. Serif fonts
Should not have
- anything cheesy, off topic, hard to read script fonts or anything that makes the label hard to read from a few feet away or too busy

```html
<!DOCTYPE html>
<html lang="en">
<head>
<meta charset="utf-8">
<title>Quailbrook Vineyards – Syrah Label</title>
<link rel="stylesheet" href="https://fonts.googleapis.com/css2?family=Cinzel:wght@600&family=Mr+Dafoe&family=Montserrat:wght@500&display=swap">
<style>
  :root {
    --paper: #ffffff;
    --gold: #c9ac74;
    --wine-core: #6e0c18;
    --wine-mid: #3a050b;
    --wine-edge: #080102;
    --wood-dark: #2a140c;
    --wood-mid: #7a3f20;
    --wood-light: #a8612f;
  }
  * { margin: 0; padding: 0; box-sizing: border-box; }
  html, body {
    width: 1200px;
    height: 865px;
    overflow: hidden;
    background: var(--paper);
  }
  .canvas {
    position: relative;
    width: 1200px;
    height: 865px;
  }
  .label {
    position: absolute;
    left: 280px;
    top: 112px;
    width: 640px;
    height: 640px;
    overflow: hidden;
  }
  .label-art {
    position: absolute;
    inset: 0;
    width: 640px;
    height: 640px;
  }
  .brand {
    position: absolute;
    left: 0;
    width: 360px;
    text-align: center;
    font-family: "Cinzel", Georgia, serif;
    font-weight: 600;
    color: var(--gold);
    line-height: 1;
  }
  .brand-name { top: 176px; font-size: 30px; letter-spacing: 0.5px; }
  .brand-sub { top: 213px; font-size: 19px; letter-spacing: 1px; }
  .varietal {
    position: absolute;
    left: 60px;
    top: 245px;
    width: 520px;
    text-align: center;
    font-family: "Mr Dafoe", "Brush Script MT", cursive;
    font-size: 165px;
    line-height: 1;
    color: var(--gold);
  }
  .vintage, .appellation {
    position: absolute;
    left: 330px;
    width: 300px;
    text-align: center;
    font-family: "Montserrat", Arial, sans-serif;
    font-weight: 500;
    color: var(--gold);
    line-height: 1;
  }
  .vintage { top: 474px; font-size: 34px; letter-spacing: 2px; }
  .appellation { top: 525px; font-size: 17px; letter-spacing: 1.5px; }
</style>
</head>
<body>
<main class="canvas">
  <section class="label">
    <svg class="label-art" viewBox="0 0 750 750" xmlns="http://www.w3.org/2000/svg">
      <defs>
        <radialGradient id="wineGlow" cx="0.47" cy="0.43" r="0.62">
          <stop offset="0" stop-color="var(--wine-core)"/>
          <stop offset="0.55" stop-color="var(--wine-mid)"/>
          <stop offset="1" stop-color="var(--wine-edge)"/>
        </radialGradient>
        <linearGradient id="woodTop" x1="0" y1="0" x2="1" y2="1">
          <stop offset="0" stop-color="var(--wood-dark)"/>
          <stop offset="0.45" stop-color="var(--wood-mid)"/>
          <stop offset="0.75" stop-color="var(--wood-light)"/>
          <stop offset="1" stop-color="var(--wood-dark)"/>
        </linearGradient>
        <linearGradient id="woodBottom" x1="0" y1="0" x2="1" y2="1">
          <stop offset="0" stop-color="var(--wood-mid)"/>
          <stop offset="0.4" stop-color="var(--wood-light)"/>
          <stop offset="0.8" stop-color="var(--wood-mid)"/>
          <stop offset="1" stop-color="var(--wood-dark)"/>
        </linearGradient>
      </defs>

      <rect class="wine-field" width="750" height="750" fill="url(#wineGlow)"/>

      <path class="wood-band wood-band--top" role="img" aria-label="Wood grain band along the top edge"
        fill="url(#woodTop)"
        d="M0 0 H750 V245 C700 232 640 215 560 190 C480 165 430 110 350 82 C300 64 260 62 200 70 C140 78 80 84 40 80 C15 76 4 64 0 50 Z"/>

      <path class="wood-band wood-band--bottom" role="img" aria-label="Wood grain band along the bottom edge"
        fill="url(#woodBottom)"
        d="M0 560 C20 580 80 592 160 586 C230 582 280 605 330 640 C390 680 470 712 560 722 C640 730 700 738 750 750 H0 Z"/>

      <g class="gold-frame" stroke="var(--gold)" stroke-width="5" fill="none">
        <line x1="20" y1="76" x2="20" y2="576"/>
        <line x1="730" y1="245" x2="730" y2="730"/>
        <line x1="650" y1="730" x2="732" y2="730"/>
      </g>

      <circle class="brand-mark" cx="211" cy="138" r="48" fill="none" stroke="var(--gold)" stroke-width="5"/>
    </svg>

    <p class="brand brand-name">QUAILBROOK</p>
    <p class="brand brand-sub">VINEYARDS</p>
    <h1 class="varietal">Syrah</h1>
    <p class="vintage">2024</p>
    <p class="appellation">WILLAMETTE VALLEY</p>
  </section>
</main>
</body>
</html>
```